Spring Detox sale graphics for social media

You MUST read the Brief in the WORD document and follow the instructions there. I want to create 10 social media graphics (new Instagram size 4:5 (1080 x 1350 pixels) focusing on our Mother’s Day Spring Detox Sale graphics, using any of the pics attached. Use the attached pics, NO RANDOM STOCK PHOTOGRAPHY. For the color scheme of the graphics, they should all be complementary to the product colors or feel like Spring time.

Target Market(s)

primarily women

Requirements
Must have
• the photos and text attached

```html
<!DOCTYPE html>
<html lang="en">
<head>
<meta charset="utf-8">
<title>Mother's Day Spring Detox Sale – Social Set</title>
<link rel="stylesheet" href="https://fonts.googleapis.com/css2?family=Arimo:wght@400;700&display=swap">
<style>
  :root {
    --mint: #e4efe5;
    --leaf: #3e7f2f;
    --leaf-text: #3f8a2e;
    --ink: #151515;
    --white: #ffffff;
    --orchid: #b12a8f;
    --crimson: #da1a24;
    --sky: #3a96b8;
    --jade: #00a070;
    --marigold: #f0aa45;
    --pale: #e6efe6;
    --tick: #2f8a2a;
    --bottles: linear-gradient(90deg, #dfe3f2 0%, #e9ecef 18%, #d6ebe3 34%, #f1f1f1 50%, #f6d6d6 62%, #f1f1f1 72%, #ecd8e9 88%, #e7d3e6 100%);
  }
  * { box-sizing: border-box; margin: 0; padding: 0; }
  html, body { width: 1200px; height: 1126px; overflow: hidden; background: var(--white); }
  body { position: relative; font-family: "Arimo", Arial, sans-serif; font-weight: 700; }

  .tile { position: absolute; width: 280px; height: 349px; overflow: hidden; background: var(--mint); }
  .line { position: absolute; left: 0; right: 0; text-align: center; line-height: 1; white-space: nowrap; }
  .header-band { position: absolute; left: 0; top: 0; width: 100%; height: 112px; }
  .product-shot { position: absolute; border-radius: 10px 10px 6px 6px; background: var(--bottles); box-shadow: 0 4px 8px rgba(0,0,0,0.08); }
  .scene { position: absolute; left: 0; width: 100%; }
  .footer-band { position: absolute; left: 6px; width: 268px; height: 30px; display: flex; align-items: center; justify-content: center; color: var(--white); font-size: 19.5px; line-height: 1; white-space: nowrap; }
  .split-band { position: absolute; left: 7px; width: 266px; height: 25px; overflow: visible; }
  .split-band text { font-family: "Arimo", Arial, sans-serif; font-weight: 700; font-size: 15.5px; }

  .headline-xl { font-size: 42px; letter-spacing: -0.5px; }
  .headline-caps { font-size: 25px; letter-spacing: -0.3px; }

  .hero-photo { position: absolute; inset: 0; background: linear-gradient(180deg, #e4ece6 0%, #efefed 30%, #f4f4f2 48%, #3a3a3a 62%, #e9e7e4 72%, #d7d3ce 100%); }
  .hero-offer { position: absolute; left: 24px; top: 18px; font-size: 33px; line-height: 1.18; color: var(--ink); }
  .hero-event { position: absolute; left: 23px; top: 94px; font-size: 26px; line-height: 1; color: var(--leaf-text); }

  .tick-row { position: absolute; left: 0; top: 219px; width: 280px; height: 32px; }
</style>
</head>
<body>

<!-- Row 1 -->
<section class="tile" style="left:20px;top:23px;">
  <div class="hero-photo" role="img" aria-label="Smiling woman in a white top and black trousers presenting the full supplement range on a marble counter"></div>
  <div class="product-shot" style="left:40px;top:210px;width:210px;height:82px;" role="img" aria-label="Row of supplement bottles and cream tubes on the counter"></div>
  <div class="hero-offer">25%<br>OFF</div>
  <div class="hero-event">Mother’s Day Sale:</div>
  <div class="footer-band" style="top:306px;height:29px;font-size:16px;background:var(--leaf);">Spring Detox for a Summer Body</div>
</section>

<section class="tile" style="left:313px;top:23px;">
  <div class="line" style="top:25px;font-size:29px;color:var(--leaf-text);">25% OFF</div>
  <div class="line" style="top:57px;font-size:29px;color:var(--ink);">Mother’s Day</div>
  <div class="product-shot" style="left:35px;top:104px;width:208px;height:124px;" role="img" aria-label="SugarEase, HormoneEase, TummyEase and LiverEase supplement bottles"></div>
  <div class="footer-band" style="top:275px;background:var(--leaf);">Spring Detox Sale</div>
</section>

<section class="tile" style="left:607px;top:23px;background:linear-gradient(200deg,#2fb845 0%,#9ad79a 30%,#e4efe5 65%);">
  <div class="line" style="top:26px;font-size:29px;color:var(--ink);">25% OFF</div>
  <div class="line" style="top:58px;font-size:29px;color:var(--ink);">All Supplements</div>
  <div class="product-shot" style="left:35px;top:104px;width:208px;height:124px;" role="img" aria-label="SugarEase, HormoneEase, TummyEase and LiverEase supplement bottles"></div>
  <div class="footer-band" style="top:275px;background:var(--leaf);">Spring Detox Sale!</div>
</section>

<!-- Row 2 -->
<section class="tile" style="left:20px;top:390px;">
  <div class="header-band" style="background:var(--orchid);"></div>
  <div class="line headline-xl" style="top:16px;color:var(--pale);">25% OFF</div>
  <div class="line headline-caps" style="top:59px;color:var(--pale);">SPRING DETOX SALE:</div>
  <div class="scene" style="top:112px;height:158px;background:linear-gradient(180deg,#e9b7d9 0%,#f5e6f1 45%,#dde8e0 100%);" role="img" aria-label="Soft pink spring sky backdrop"></div>
  <div class="product-shot" style="left:14px;top:140px;width:252px;height:108px;" role="img" aria-label="LiverEase, TummyEase, HormoneEase and SugarEase bottles"></div>
  <svg class="split-band" style="top:280px;" viewBox="0 0 266 25">
    <polygon points="0,0 128,0 137,25 0,25" fill="var(--orchid)"/>
    <polygon points="134,0 266,0 266,25 143,25" fill="var(--orchid)"/>
    <text x="62" y="18" text-anchor="middle" fill="var(--white)">Spring Reset</text>
    <text x="203" y="18" text-anchor="middle" fill="var(--white)">Summer Ready</text>
  </svg>
</section>

<section class="tile" style="left:313px;top:390px;">
  <div class="header-band" style="background:var(--leaf);"></div>
  <div class="line headline-xl" style="top:16px;color:var(--pale);">25% OFF</div>
  <div class="line headline-caps" style="top:59px;color:var(--pale);">MOTHER’S DAY SALE:</div>
  <div class="product-shot" style="left:27px;top:128px;width:230px;height:132px;" role="img" aria-label="SugarEase, HormoneEase, TummyEase and LiverEase supplement bottles"></div>
  <div class="footer-band" style="top:276px;height:23px;left:8px;width:264px;background:var(--leaf);font-size:16.5px;">Feel Amazing Again!</div>
</section>

<section class="tile" style="left:607px;top:390px;">
  <div class="header-band" style="height:110px;background:var(--crimson);"></div>
  <div class="line headline-xl" style="top:13px;color:var(--pale);">25% OFF</div>
  <div class="line" style="top:60px;font-size:39px;color:var(--pale);">Everything:</div>
  <div class="product-shot" style="left:13px;top:128px;width:254px;height:118px;" role="img" aria-label="LiverEase, TummyEase, HormoneEase and SugarEase supplement bottles in a row"></div>
  <div class="footer-band" style="top:276px;height:23px;left:8px;width:264px;background:var(--crimson);font-size:15.5px;">Mother’s Day Spring Detox Sale</div>
</section>

<section class="tile" style="left:900px;top:390px;">
  <div class="line" style="top:25px;font-size:33px;color:var(--ink);">Mother’s Day</div>
  <div class="line" style="top:60px;font-size:22.5px;color:var(--leaf-text);">Spring Detox Sale:</div>
  <div class="product-shot" style="left:23px;top:111px;width:56px;height:99px;background:linear-gradient(180deg,#f7f7f5 30%,#e5c9e0);" role="img" aria-label="LiverEase bottle"></div>
  <div class="product-shot" style="left:86px;top:111px;width:56px;height:99px;background:linear-gradient(180deg,#f7f7f5 30%,#f0c8cb);" role="img" aria-label="TummyEase bottle"></div>
  <div class="product-shot" style="left:146px;top:111px;width:56px;height:99px;background:linear-gradient(180deg,#f7f7f5 30%,#c8e3d9);" role="img" aria-label="HormoneEase bottle"></div>
  <div class="product-shot" style="left:210px;top:115px;width:48px;height:95px;background:linear-gradient(180deg,#f7f7f5 30%,#cbd3ec);" role="img" aria-label="SugarEase bottle"></div>
  <svg class="tick-row" viewBox="0 0 280 32">
    <g fill="var(--tick)">
      <circle cx="53" cy="16" r="15"/><circle cx="113" cy="16" r="15"/>
      <circle cx="174" cy="16" r="15"/><circle cx="234" cy="16" r="15"/>
    </g>
    <g fill="none" stroke="var(--white)" stroke-width="2" stroke-linecap="round" stroke-linejoin="round">
      <path d="M46 16 l5 7 l9 -14"/><path d="M106 16 l5 7 l9 -14"/>
      <path d="M167 16 l5 7 l9 -14"/><path d="M227 16 l5 7 l9 -14"/>
    </g>
  </svg>
  <div class="footer-band" style="top:274px;left:6px;width:268px;background:var(--leaf);font-size:18.5px;">25% Off Everything!</div>
</section>

<!-- Row 3 -->
<section class="tile" style="left:20px;top:756px;">
  <div class="header-band" style="background:var(--sky);"></div>
  <div class="line headline-xl" style="top:16px;color:var(--pale);">25% OFF</div>
  <div class="line headline-caps" style="top:59px;color:var(--pale);">MOTHER’S DAY SALE:</div>
  <div class="scene" style="top:112px;height:158px;background:linear-gradient(180deg,#9fd0e0 0%,#eef6f5 50%,#dde8e0 100%);" role="img" aria-label="Soft blue sky backdrop"></div>
  <div class="product-shot" style="left:27px;top:128px;width:230px;height:132px;" role="img" aria-label="SugarEase, HormoneEase, TummyEase and LiverEase supplement bottles"></div>
  <div class="footer-band" style="top:276px;height:23px;left:7px;width:264px;background:var(--sky);font-size:16.5px;">Refresh Your Body</div>
</section>

<section class="tile" style="left:313px;top:756px;">
  <div class="header-band" style="background:var(--jade);"></div>
  <div class="line headline-xl" style="top:16px;color:var(--pale);">25% OFF</div>
  <div class="line headline-caps" style="top:59px;color:var(--pale);">SPRING DETOX SALE:</div>
  <div class="scene" style="top:112px;height:158px;background:linear-gradient(160deg,#d9f0d6 0%,#f3f8f1 40%,#b9e1bd 100%);" role="img" aria-label="Bright green spring light backdrop"></div>
  <div class="product-shot" style="left:27px;top:128px;width:230px;height:132px;" role="img" aria-label="SugarEase, HormoneEase, TummyEase and LiverEase supplement bottles"></div>
  <svg class="split-band" style="top:275px;left:8px;width:264px;" viewBox="0 0 264 25">
    <polygon points="0,0 126,0 135,25 0,25" fill="var(--jade)"/>
    <polygon points="132,0 264,0 264,25 141,25" fill="var(--jade)"/>
    <text x="63" y="18" text-anchor="middle" fill="var(--white)">Spring Cleanse</text>
    <text x="200" y="18" text-anchor="middle" fill="var(--white)">Summer Glow</text>
  </svg>
</section>

<section class="tile" style="left:607px;top:756px;">
  <div class="header-band" style="background:var(--marigold);"></div>
  <div class="line headline-xl" style="top:16px;color:var(--pale);">25% OFF</div>
  <div class="line headline-caps" style="top:59px;color:var(--pale);">MOTHER’S DAY SALE:</div>
  <div class="product-shot" style="left:27px;top:128px;width:230px;height:132px;" role="img" aria-label="SugarEase, HormoneEase, TummyEase and LiverEase supplement bottles"></div>
  <svg class="split-band" style="top:275px;left:8px;width:264px;" viewBox="0 0 264 25">
    <polygon points="0,0 126,0 135,25 0,25" fill="var(--marigold)"/>
    <polygon points="132,0 264,0 264,25 141,25" fill="var(--marigold)"/>
    <text x="64" y="17.5" text-anchor="middle" fill="var(--pale)" style="font-size:12.5px;">Detox This Spring.</text>
    <text x="202" y="17.5" text-anchor="middle" fill="var(--pale)" style="font-size:12.5px;">Shine This Summer</text>
  </svg>
</section>

</body>
</html>
```